Retail Jewelry Business Card Design Project

We are in need of a new business card design for a retail jewelry store. This store is in the business of fine jewelry including but not specific to bridal jewelry, diamonds, designer jewelry and watches.

This store has been in business for 20 years but continues to strive for a modern professional appeal. The main colors use for this business are a royal blue, white and silver.

Target Market(s)

Target market is ages 18-50

Industry/Entity Type

Jewelry

Requirements
Must have
• Sales Person Name
Sales Person Email Address

Store Address
Store Phone
Website

Standard business card size. No odd shapes or sizes.
Nice to have
• Overall modern feel for card.

We have thought that a design with a nice feature of the logo on the back of the card would be nice but open to ideas.
Should not have
• No specific images of jewelry should be used.

```html
<!DOCTYPE html>
<html lang="en">
<head>
<meta charset="utf-8">
<title>Marlow Kent Fine Jewelry – Business Cards</title>
<link rel="stylesheet" href="https://fonts.googleapis.com/css2?family=Jost:wght@400;500;600&display=swap">
<style>
  :root {
    --royal-blue: #2e3a8f;
    --white: #ffffff;
    --ink: #2a2f5c;
    --backdrop: #e9e9ec;
    --shadow: rgba(20, 24, 60, 0.18);
  }
  * { box-sizing: border-box; margin: 0; padding: 0; }
  html, body {
    width: 1200px;
    height: 750px;
    overflow: hidden;
    background: var(--backdrop);
    font-family: "Jost", "Futura", sans-serif;
  }
  .sheet {
    position: relative;
    width: 1200px;
    height: 750px;
    display: flex;
    align-items: center;
    justify-content: center;
    gap: 60px;
  }
  .card {
    position: relative;
    width: 500px;
    height: 286px;
    box-shadow: 0 8px 22px var(--shadow);
    overflow: hidden;
  }

  /* Front */
  .card-front { background: var(--white); }
  .front-top {
    height: 158px;
    display: flex;
    flex-direction: column;
    align-items: center;
    padding-top: 34px;
  }
  .brand-name {
    font-weight: 500;
    font-size: 40px;
    letter-spacing: 1px;
    color: var(--royal-blue);
    line-height: 1;
  }
  .brand-name.small-caps-line {
    font-size: 20px;
    letter-spacing: 4px;
    margin-top: 8px;
    text-transform: uppercase;
  }
  .store-address {
    margin-top: auto;
    margin-bottom: 10px;
    font-size: 13px;
    letter-spacing: 0.6px;
    color: var(--ink);
  }
  .front-band {
    height: 128px;
    background: var(--royal-blue);
    color: var(--white);
    padding: 16px 24px;
  }
  .person-name {
    font-weight: 600;
    font-size: 18px;
    margin-bottom: 8px;
  }
  .contact-list { list-style: none; }
  .contact-list li {
    display: flex;
    align-items: center;
    gap: 7px;
    font-size: 13.5px;
    line-height: 1.55;
  }
  .contact-list svg { width: 11px; height: 11px; flex: none; }

  /* Back */
  .card-back {
    background: var(--royal-blue);
    color: var(--white);
    display: flex;
    flex-direction: column;
    align-items: center;
    justify-content: center;
  }
  .card-back .brand-name { color: var(--white); font-size: 46px; }
  .card-back .brand-name.small-caps-line { font-size: 22px; margin-top: 10px; }
  .back-web {
    margin-top: 34px;
    font-size: 13px;
    letter-spacing: 3px;
  }
</style>
</head>
<body>
  <main class="sheet">
    <section class="card card-front" aria-label="Business card front">
      <div class="front-top">
        <p class="brand-name">Marlow Kent</p>
        <p class="brand-name small-caps-line">Fine Jewelry</p>
        <p class="store-address">2875 Linden Avenue, Bay Harbor, FL 32590</p>
      </div>
      <div class="front-band">
        <p class="person-name">Marlow Kent Avery</p>
        <ul class="contact-list">
          <li>
            <svg viewBox="0 0 12 12" aria-hidden="true"><circle cx="6" cy="6" r="5.2" fill="none" stroke="currentColor" stroke-width="1"/><path d="M4 3.2l1 1.2-.6.8c.4.9 1 1.5 1.9 1.9l.8-.6 1.2 1-.6 1c-2.3-.3-4.1-2.1-4.4-4.4z" fill="currentColor"/></svg>
            555-014-2290
          </li>
          <li>
            <svg viewBox="0 0 12 12" aria-hidden="true"><rect x="1" y="3" width="10" height="7" fill="currentColor"/><path d="M1 3l5 4 5-4" fill="none" stroke="#2e3a8f" stroke-width="1"/></svg>
            marlow@marlowkentjewelry.com
          </li>
          <li>
            <svg viewBox="0 0 12 12" aria-hidden="true"><circle cx="6" cy="6" r="5" fill="none" stroke="currentColor" stroke-width="1"/><ellipse cx="6" cy="6" rx="2.2" ry="5" fill="none" stroke="currentColor" stroke-width="0.8"/><path d="M1 6h10M2 3.5h8M2 8.5h8" stroke="currentColor" stroke-width="0.8"/></svg>
            www.marlowkentjewelry.com
          </li>
        </ul>
      </div>
    </section>

    <section class="card card-back" aria-label="Business card back">
      <p class="brand-name">Marlow Kent</p>
      <p class="brand-name small-caps-line">Fine Jewelry</p>
      <p class="back-web">www.marlowkentjewelry.com</p>
    </section>
  </main>
</body>
</html>
```